Mindfulness School for Children -- Business Cards

We're looking for business cards for our school directors and owners. We're a mindfulness school for children called little lanterns. Attached are our logos/icons.

```html
<!DOCTYPE html>
<html lang="en">
<head>
<meta charset="utf-8">
<title>Little Lanterns – Business Cards</title>
<link href="https://fonts.googleapis.com/css2?family=Karla:wght@400;500;700&display=swap" rel="stylesheet">
<style>
  :root {
    --backdrop: #7f7f7f;
    --paper: #ffffff;
    --sky: #52acc2;
    --sage: #8dca96;
    --teal: #2ba2b7;
    --brand: #4aa3b6;
    --ink-light: #ffffff;
  }
  * { box-sizing: border-box; margin: 0; padding: 0; }
  html, body {
    width: 1133px; height: 1200px; overflow: hidden;
    background: var(--backdrop);
    font-family: "Karla", sans-serif;
  }
  .card { position: absolute; overflow: hidden; }

  /* Front */
  .card-front {
    left: 218px; top: 153px; width: 697px; height: 397px;
    background: var(--paper);
  }
  .brand-area {
    height: 255px; display: flex; align-items: center; justify-content: center;
    padding-top: 18px;
  }
  .wordmark {
    font-size: 46px; font-weight: 500; color: var(--brand);
    letter-spacing: 0.01em;
  }
  .info-band {
    position: absolute; left: 0; bottom: 0; width: 100%; height: 142px;
    display: flex; gap: 3px; background: var(--paper);
  }
  .person {
    flex: 0 0 347px; background: var(--sky); color: var(--ink-light);
    padding: 20px 0 0 47px;
  }
  .person-name { font-size: 22px; font-weight: 700; letter-spacing: 0.04em; line-height: 1.1; }
  .person-title { font-size: 14.5px; letter-spacing: 0.03em; line-height: 1.2; }
  .person-address { margin-top: 12px; font-size: 15px; line-height: 20px; letter-spacing: 0.02em; }
  .contact {
    flex: 1; background: var(--sage); color: var(--ink-light);
    padding: 33px 50px 0 0; list-style: none;
  }
  .contact li {
    display: flex; justify-content: flex-end; align-items: center; gap: 5px;
    font-size: 14.5px; line-height: 20px; letter-spacing: 0.02em;
  }
  .contact svg { width: 13px; height: 13px; flex: none; }

  /* Back */
  .card-back {
    left: 201px; top: 640px; width: 714px; height: 407px;
    background: var(--teal); color: var(--ink-light); text-align: center;
  }
  .back-mark {
    position: absolute; left: 0; right: 0; top: 90px;
    display: flex; flex-direction: column; align-items: center; gap: 22px;
  }
  .back-dot { width: 96px; height: 96px; border-radius: 50%; background: var(--ink-light); }
  .back-name { font-size: 40px; font-weight: 500; letter-spacing: 0.02em; }
  .back-url {
    position: absolute; left: 0; right: 0; top: 348px;
    font-size: 16px; letter-spacing: 0.27em;
  }
</style>
</head>
<body>

<section class="card card-front">
  <div class="brand-area">
    <span class="wordmark">littlelanterns</span>
  </div>
  <div class="info-band">
    <div class="person">
      <p class="person-name">DANIEL HAYES</p>
      <p class="person-title">President</p>
      <p class="person-address">412 Willow Court<br>Fairbanks, Alaska 99701</p>
    </div>
    <ul class="contact">
      <li>555-214-7730
        <svg viewBox="0 0 16 16" aria-hidden="true"><path fill="#fff" d="M3.6 1.2l2.3 2.6-1.3 1.9c.9 2 2.5 3.7 4.6 4.6l1.9-1.3 2.6 2.3-1.4 2.5C7 13.6 2.4 9 1.2 2.6z"/></svg>
      </li>
      <li>555-318-4092
        <svg viewBox="0 0 16 16" aria-hidden="true"><rect x="4" y="1" width="8" height="14" rx="1.5" fill="none" stroke="#fff" stroke-width="1.6"/><circle cx="8" cy="12.5" r="0.9" fill="#fff"/></svg>
      </li>
      <li>name@littlelanterns.com
        <svg viewBox="0 0 16 16" aria-hidden="true"><rect x="1" y="3.5" width="14" height="9" fill="#fff"/><path d="M1.5 4l6.5 5 6.5-5" fill="none" stroke="#8dca96" stroke-width="1.2"/></svg>
      </li>
      <li>www.littlelanterns.com
        <svg viewBox="0 0 16 16" aria-hidden="true"><circle cx="8" cy="8" r="6.8" fill="#fff"/><path d="M5 4.5c1.5.3 2 1.5 1.2 2.5-.7.8.2 1.8 1.3 1.8M10.5 11c-.6-1 0-2 1.2-2.2" fill="none" stroke="#8dca96" stroke-width="1.3"/></svg>
      </li>
    </ul>
  </div>
</section>

<section class="card card-back">
  <div class="back-mark">
    <span class="back-dot"></span>
    <span class="back-name">littlelanterns</span>
  </div>
  <p class="back-url">www.LittleLanterns.com</p>
</section>

</body>
</html>
```